Fenwick Ridge Accounting - New client package

I need a stationary package (presentation folder cover, welcome letter template/design, sample financial report template/design, business card and new logo) for my accounting business. I would like to see designs that use the color blue. Financial icons can be included in the design. The final design should be clean and communicate professionalism and the use of modern; user-friendly technology. Attached postcard files should help with overall design concept.

```html
<!DOCTYPE html>
<html lang="en">
<head>
<meta charset="utf-8">
<title>Fenwick Ridge Accounting – Presentation Folder</title>
<link rel="stylesheet" href="https://fonts.googleapis.com/css2?family=Tinos:wght@400;700&family=Open+Sans:wght@400;600&family=Montserrat:wght@400;500&display=swap">
<style>
  :root {
    --navy-top: #0e5883;
    --navy-bottom: #073150;
    --navy-pocket: #0a4069;
    --paper: #ffffff;
    --paper-shade: #e9ebee;
    --backdrop: #dcdcdc;
    --watermark: #eceef1;
    --ink: #1b1b1b;
    --white: #ffffff;
  }
  * { box-sizing: border-box; margin: 0; padding: 0; }
  html, body { width: 1200px; height: 1200px; overflow: hidden; }
  body {
    background: radial-gradient(circle at 50% 45%, #f1f1f1 0%, var(--backdrop) 75%);
    position: relative;
    font-family: "Open Sans", sans-serif;
  }
  .spread {
    position: absolute;
    left: 90px;
    width: 810px;
    height: 540px;
    display: flex;
    box-shadow: 0 18px 40px rgba(0,0,0,0.25);
  }
  .spread--outside { top: 40px; }
  .spread--inside { top: 625px; }
  .panel {
    position: relative;
    width: 405px;
    height: 540px;
    overflow: hidden;
  }
  .panel--navy {
    background: linear-gradient(180deg, var(--navy-top) 0%, var(--navy-bottom) 100%);
    color: var(--white);
  }
  .panel--back { border-right: 1px solid rgba(0,0,0,0.25); }
  .panel--paper-left { background: linear-gradient(90deg, #fafafa 0%, #f3f4f5 80%, var(--paper-shade) 100%); }
  .panel--paper-right { background: linear-gradient(90deg, var(--paper-shade) 0%, var(--paper) 25%, var(--paper) 100%); }

  .edge-slot {
    position: absolute;
    height: 6px;
    width: 150px;
    background: var(--white);
  }
  .edge-slot--top { top: 0; }
  .edge-slot--bottom { bottom: 0; }

  .wordmark {
    position: absolute;
    left: 0; right: 0;
    text-align: center;
    font-family: "Tinos", serif;
    font-weight: 700;
    line-height: 1.05;
  }
  .wordmark__rule {
    display: block;
    width: 260px;
    height: 1px;
    margin: 10px auto 0;
    background: currentColor;
  }
  .wordmark--cover { top: 100px; font-size: 40px; }
  .wordmark--faint { top: 150px; font-size: 42px; color: var(--watermark); }

  .web {
    position: absolute;
    left: 0; right: 0;
    text-align: center;
    font-family: "Montserrat", sans-serif;
    letter-spacing: 4px;
    text-transform: uppercase;
  }
  .web--cover { bottom: 42px; font-size: 11px; }

  .contact {
    position: absolute;
    left: 36px;
    bottom: 32px;
    font-family: "Tinos", serif;
    font-size: 13px;
  }
  .contact__title {
    font-size: 14px;
    letter-spacing: 0.5px;
    padding-bottom: 4px;
    border-bottom: 1px solid var(--white);
    display: inline-block;
    margin-bottom: 10px;
  }
  .contact__row { display: flex; align-items: center; gap: 10px; margin-top: 6px; }
  .contact__row svg { width: 12px; height: 12px; fill: var(--white); }

  .social {
    position: absolute;
    right: 24px;
    bottom: 40px;
    display: flex;
    gap: 8px;
  }
  .social__dot { width: 28px; height: 28px; border-radius: 50%; background: var(--white); }

  .pocket {
    position: absolute;
    bottom: 0;
    height: 150px;
    width: 100%;
    background: var(--navy-pocket);
    box-shadow: 0 -4px 10px rgba(0,0,0,0.12);
  }
  .pocket--left { left: 0; border-top-right-radius: 26px; width: 370px; }
  .pocket--right { right: 0; border-top-left-radius: 26px; width: 370px; }
  .pocket__note {
    position: absolute;
    left: 40px;
    top: 72px;
    color: var(--white);
    font-size: 13px;
    letter-spacing: 0.5px;
    text-transform: uppercase;
  }

  .card {
    position: absolute;
    left: 140px;
    top: 30px;
    width: 180px;
    height: 104px;
    background: linear-gradient(135deg, #155f8c 0%, #0b3d62 100%);
    box-shadow: 0 3px 8px rgba(0,0,0,0.35);
    color: var(--white);
    clip-path: polygon(0 0, 100% 0, 100% 88%, 94% 100%, 0 100%, 0 12%);
  }
  .card__name {
    position: absolute;
    top: 26px; left: 0; right: 0;
    text-align: center;
    font-family: "Tinos", serif;
    font-weight: 700;
    font-size: 13px;
    line-height: 1.1;
  }
  .card__web {
    position: absolute;
    bottom: 16px; left: 0; right: 0;
    text-align: center;
    font-family: "Montserrat", sans-serif;
    font-size: 5.5px;
    letter-spacing: 1.5px;
    text-transform: uppercase;
  }
  .card__bar {
    position: absolute;
    left: 60px;
    width: 60px;
    height: 2px;
    background: var(--white);
  }

  .view-label {
    position: absolute;
    left: 960px;
    font-family: "Open Sans", sans-serif;
    font-size: 28px;
    color: var(--ink);
    letter-spacing: 0.5px;
  }
  .view-label--outside { top: 198px; }
  .view-label--inside { top: 770px; }
</style>
</head>
<body>

  <section class="spread spread--outside" aria-label="Folder outside">
    <div class="panel panel--navy panel--back">
      <span class="edge-slot edge-slot--top" style="left:110px"></span>
      <div class="contact">
        <div class="contact__title">CONTACT US</div>
        <div class="contact__row">
          <svg viewBox="0 0 24 24"><path d="M6.6 10.8a15.2 15.2 0 0 0 6.6 6.6l2.2-2.2a1 1 0 0 1 1-.25 11.4 11.4 0 0 0 3.6.57 1 1 0 0 1 1 1V20a1 1 0 0 1-1 1A17 17 0 0 1 3 4a1 1 0 0 1 1-1h3.5a1 1 0 0 1 1 1c0 1.25.2 2.45.57 3.57a1 1 0 0 1-.25 1z"/></svg>
          <span>1.800.555.0142</span>
        </div>
        <div class="contact__row">
          <svg viewBox="0 0 24 24"><path d="M2 5h20v14H2z M2 5l10 8 10-8" stroke="#073150" stroke-width="1.5"/></svg>
          <span>info@fenwickridgeaccounting.com</span>
        </div>
        <div class="contact__row">
          <svg viewBox="0 0 24 24"><path d="M12 2a7 7 0 0 0-7 7c0 5 7 13 7 13s7-8 7-13a7 7 0 0 0-7-7zm0 9.5A2.5 2.5 0 1 1 12 6.5a2.5 2.5 0 0 1 0 5z"/></svg>
          <span>Address</span>
        </div>
      </div>
      <div class="social" aria-label="Social profiles">
        <span class="social__dot"></span>
        <span class="social__dot"></span>
      </div>
    </div>
    <div class="panel panel--navy panel--front">
      <span class="edge-slot edge-slot--top" style="left:120px"></span>
      <div class="wordmark wordmark--cover">
        Fenwick Ridge<br>Accounting
        <span class="wordmark__rule"></span>
      </div>
      <div class="web web--cover">www.fenwickridgeaccounting.com</div>
      <span class="edge-slot edge-slot--bottom" style="left:140px"></span>
    </div>
  </section>

  <div class="view-label view-label--outside">OUTSIDE</div>

  <section class="spread spread--inside" aria-label="Folder inside">
    <div class="panel panel--paper-left">
      <div class="wordmark wordmark--faint">
        Fenwick Ridge<br>Accounting
        <span class="wordmark__rule"></span>
      </div>
      <div class="pocket pocket--left">
        <p class="pocket__note">A group photo goes here</p>
      </div>
    </div>
    <div class="panel panel--paper-right">
      <div class="wordmark wordmark--faint">
        Fenwick Ridge<br>Accounting
        <span class="wordmark__rule"></span>
      </div>
      <div class="pocket pocket--right">
        <div class="card" aria-label="Business card">
          <span class="card__bar" style="top:8px"></span>
          <div class="card__name">Fenwick Ridge<br>Accounting</div>
          <div class="card__web">www.fenwickridgeaccounting.com</div>
          <span class="card__bar" style="bottom:6px"></span>
        </div>
      </div>
    </div>
  </section>

  <div class="view-label view-label--inside">INSIDE</div>

</body>
</html>
```